Stationary Suite for Aussie Law Firm

We are a small law firm operating out of Albany, Western Australia. We have a logo, which we love and was the winner of a ArtworkHive contest last year.
We require a suite of business stationary products incorporating our logo and contact details. These should be:
1. Letterhead (A4)
The letterhead should incorporate the following information in addition to the logo:
ABN 38 602 917 255 (this is our Australian Business Number)
Beatrix Lund atf The BJL Legal Trust t/as Harbour Gate Legal & Conveyancing (legal name of the business)
Address: Wexley House, Wexley Street, Albany
Postal Address: PO Box 8147, Albany WA 6332
Telephone: 0491 670 382
Facsimile: 08 9722 5913
Email: info@harbourgatelegal.com.au
Website: www.harbourgatelegal.com.au
2. Business Card (90mm x 55mm)
I've attached my current business card layout just for your information.
The front of the business card should include the following information in addition to the logo:
Beatrix Lund
Director & Principal Solicitor
Telephone: 0491 670 382
Facsimile: 08 9722 5913
Email: beatrix@harbourgatelegal.com.au
The back of the card should be similar to the back of my existing card, but should only have the logo in white and the address of our website (www.harbourgatelegal.com.au)
3. Email signature block
This should include the same information as the front of the business card.
4. With Compliments slip (DL size)
The With Compliments slip should include the same information as the Letterhead.
5. Banner (830mm x 2000mm)
We need a banner designed for use at marketing events. This should include our website details and logo - other than that you have fairly free reign with the design.
6. Flyer (DL)
We need a flyer setting out our services and main contact details for use at marketing events. The details to be included are:
Telephone: 0491 670 382
Web: www.harbourgatelegal.com.au
Areas of law:
Wills & Estate Planning
Probate & Letters of Administration
Property Law & Conveyancing
General Commercial Law
Business Law
Style guide:
Please look at our website for an idea as to the style of designs we are looking for - www.harbourgatelegal.com.au. The design should be modern, sharp and professional.
Colours:
The CMYK details for the colours in our logo are:
Light Blue C72 M5 Y0 K0
Dark Blue C97 M72 Y16 K30
Edit 31/7/2014
I have added a couple of photos that we have used on our website, and additional photos. These are from our local area, so feel free to use these in your designs or to inform them.
- Calibri, Century Gothic

```html
<!DOCTYPE html>
<html lang="en">
<head>
<meta charset="utf-8">
<title>Harbour Gate Legal &amp; Conveyancing – Stationery Suite</title>
<link rel="stylesheet" href="https://fonts.googleapis.com/css2?family=Lato:wght@300;400;700&display=swap">
<style>
:root{
  --sky:#3fb0e6;
  --sky-soft:#8fd0f0;
  --navy:#1d4e89;
  --brand:#2a73b0;
  --ink:#2b2b2b;
  --muted:#6b6b6b;
  --paper:#ffffff;
  --mist:#eef1f4;
  --stage:#e6e7e9;
}
*{box-sizing:border-box;margin:0;padding:0}
html,body{width:1200px;height:758px;overflow:hidden}
body{background:var(--stage);font-family:"Lato",Arial,sans-serif;color:var(--ink);position:relative}
.piece{position:absolute;background:var(--paper);overflow:hidden;box-shadow:0 2px 6px rgba(0,0,0,.18)}
.wave{position:absolute;left:0;width:100%;display:block}
.brand-name{font-family:"Lato",Arial,sans-serif;font-weight:400;color:var(--brand);text-transform:uppercase;letter-spacing:.04em;line-height:1.15;display:flex;align-items:center;gap:6px}
.brand-name .dot{width:8px;height:8px;border-radius:50%;background:currentColor;flex:none}
.brand-name.on-blue{color:#fff}

/* Business card – front */
.card-front{left:58px;top:58px;width:170px;height:100px}
.card-front .brand-name{position:absolute;left:10px;top:12px;font-size:7px;width:80px}
.card-front .holder{position:absolute;right:10px;top:30px;text-align:right}
.card-front .holder-name{font-size:9.5px;color:var(--ink)}
.card-front .holder-role{font-size:4.5px;color:var(--brand)}
.card-front .wave{top:44px;height:56px}
.card-front .contact{position:absolute;right:10px;top:54px;text-align:right;color:#fff;font-size:6.5px;line-height:1.35}
.card-front .contact small{font-size:4.8px}
.card-front .address{position:absolute;left:26px;bottom:6px;color:#fff;font-size:3.6px;line-height:1.4}

/* Business card – back */
.card-back{left:58px;top:215px;width:170px;height:105px;background:var(--sky)}
.card-back .brand-name{position:absolute;left:0;right:0;top:28px;justify-content:center;font-size:10px;text-align:center}
.card-back .wave{bottom:0;height:40px}
.card-back .web{position:absolute;bottom:8px;width:100%;text-align:center;font-size:5.5px;color:var(--brand)}

/* Email signature block */
.email-sig{left:70px;top:440px;width:144px;height:200px}
.email-sig .brand-name{position:absolute;left:8px;top:26px;font-size:7.5px;width:120px}
.email-sig .holder{position:absolute;left:8px;top:58px;font-size:5px;line-height:1.4}
.email-sig .holder b{font-weight:400;color:var(--brand)}
.email-sig .wave{bottom:0;height:110px}
.email-sig .contact{position:absolute;left:8px;top:104px;font-size:6px;line-height:1.45;color:#fff}
.email-sig .contact small{font-size:4.5px}
.email-sig .address{position:absolute;left:8px;top:134px;font-size:4px;line-height:1.5;color:#fff}

/* Letterhead */
.letterhead{left:318px;top:100px;width:372px;height:526px}
.letterhead .top-wave{top:0;height:110px}
.letterhead .brand-name{position:absolute;left:52px;top:48px;font-size:13px;width:160px}
.letterhead .tel{position:absolute;right:26px;top:88px;text-align:right;font-size:5.5px;line-height:1.5}
.letterhead .body{position:absolute;left:52px;right:26px;top:150px;font-size:6.2px;line-height:1.55;text-align:justify}
.letterhead .greeting{font-size:12px;margin-bottom:16px}
.letterhead .body p{margin-bottom:10px}
.letterhead .signoff{position:absolute;right:26px;top:408px;font-size:6.5px;text-align:right}
.letterhead .signature{position:absolute;right:26px;top:422px;width:60px;height:18px;background:linear-gradient(90deg,#dfe8f2,#c9d8ea);border-radius:3px}
.letterhead .bottom-wave{bottom:0;height:92px}
.letterhead .legal{position:absolute;left:0;right:0;bottom:56px;text-align:center;color:var(--navy);font-size:5.5px;line-height:1.5}
.letterhead .foot{position:absolute;left:38px;right:26px;bottom:22px;display:flex;justify-content:space-between;color:var(--navy);font-size:5.2px;line-height:1.6}

/* With compliments slip */
.comp-slip{left:776px;top:75px;width:392px;height:188px}
.comp-slip .wave{top:20px;height:168px}
.comp-slip .brand-name{position:absolute;left:14px;top:26px;font-size:9px;width:110px}
.comp-slip .headline{position:absolute;left:0;right:0;top:86px;text-align:center;color:#fff;font-size:19px;font-weight:300;letter-spacing:.02em;text-shadow:0 0 8px rgba(255,255,255,.7)}
.comp-slip .legal{position:absolute;left:0;right:0;top:136px;text-align:center;color:var(--navy);font-size:5.3px;line-height:1.5}
.comp-slip .contacts{position:absolute;left:40px;right:20px;top:156px;display:flex;justify-content:space-between;color:#fff;font-size:5px;line-height:1.6}
.comp-slip .contacts b{font-weight:700}

/* Flyer */
.flyer{left:770px;top:388px;width:400px;height:200px}
.flyer .photo{position:absolute;inset:0;background:linear-gradient(135deg,#2f8fc9 0%,#54b6e6 45%,#1f78b5 100%)}
.flyer .cap{top:0;height:86px}
.flyer .brand-name{position:absolute;left:14px;top:30px;font-size:10px;width:110px}
.flyer .services{position:absolute;right:0;top:22px;width:230px;list-style:none}
.flyer .services li{background:rgba(255,255,255,.88);color:var(--navy);font-size:12px;padding:3px 10px;margin-bottom:6px}
.flyer .tel{position:absolute;right:14px;bottom:24px;color:#fff;font-size:13px;font-weight:300}
.flyer .links{position:absolute;right:14px;bottom:9px;color:#fff;font-size:7.5px;display:flex;gap:14px}
</style>
</head>
<body>

<!-- Business card front -->
<section class="piece card-front" aria-label="Business card front">
  <div class="brand-name"><span class="dot"></span><span>Harbour Gate Legal &amp; Conveyancing</span></div>
  <div class="holder">
    <div class="holder-name">Beatrix Lund</div>
    <div class="holder-role">Director &amp; Principal Solicitor</div>
  </div>
  <svg class="wave" viewBox="0 0 170 56" preserveAspectRatio="none" aria-hidden="true">
    <path d="M0 26 C50 4 110 24 170 2 V56 H0 Z" fill="var(--sky)"/>
  </svg>
  <div class="contact">
    <div><small>t:</small> 0491 670 382</div>
    <div><small>f:</small> 08 9722 5913</div>
    <div><small>e: beatrix@harbourgatelegal.com.au</small></div>
  </div>
  <div class="address">Wexley House, Wexley Street, Albany<br>PO Box 8147, Albany WA 6332</div>
</section>

<!-- Business card back -->
<section class="piece card-back" aria-label="Business card back">
  <div class="brand-name on-blue"><span class="dot"></span><span>Harbour Gate<br>Legal &amp; Conveyancing</span></div>
  <svg class="wave" viewBox="0 0 170 40" preserveAspectRatio="none" aria-hidden="true">
    <path d="M0 20 C60 0 110 28 170 8 V40 H0 Z" fill="var(--paper)"/>
  </svg>
  <div class="web">www.harbourgatelegal.com.au</div>
</section>

<!-- Email signature block -->
<section class="piece email-sig" aria-label="Email signature block">
  <div class="brand-name"><span class="dot"></span><span>Harbour Gate<br>Legal &amp; Conveyancing</span></div>
  <div class="holder">Beatrix Lund<br><b>Director &amp; Principal Solicitor</b></div>
  <svg class="wave" viewBox="0 0 144 110" preserveAspectRatio="none" aria-hidden="true">
    <path d="M0 30 C50 8 100 40 144 14 V110 H0 Z" fill="var(--sky)"/>
  </svg>
  <div class="contact">
    <div><small>t:</small> 0491 670 382 &nbsp;<small>f:</small> 08 9722 5913</div>
    <div><small>e: beatrix@harbourgatelegal.com.au</small></div>
  </div>
  <div class="address">Wexley House, Wexley Street, Albany<br>PO Box 8147, Albany WA 6332</div>
</section>

<!-- Letterhead -->
<section class="piece letterhead" aria-label="Letterhead">
  <svg class="wave top-wave" viewBox="0 0 372 110" preserveAspectRatio="none" aria-hidden="true">
    <path d="M0 0 H372 V60 C310 40 270 50 240 80 C210 110 150 110 0 104 Z" fill="var(--mist)"/>
    <path d="M240 80 C270 50 310 40 372 60 V110 H0 C150 110 210 110 240 80 Z" fill="var(--paper)"/>
  </svg>
  <div class="brand-name"><span class="dot"></span><span>Harbour Gate<br>Legal &amp; Conveyancing</span></div>
  <div class="tel">Telephone: 0491 670 382<br>Facsimile: 08 9722 5913</div>
  <div class="body">
    <div class="greeting">Dear Mr. Hollis,</div>
    <p>Lorem ipsum dolor sit amet, consectetur adipiscing elit. Donec orci purus, luctus vitae dignissim eu, iaculis sed purus. Vivamus faucibus, ipsum nec aliquet viverra, leo mauris condimentum ligula, sit amet sagittis enim ligula quis arcu. Nam egestas tortor id nisi porttitor mattis. In tortor ante, ultricies in suscipit a, tempus non massa. Vivamus et auctor mi. Fusce vel massa nulla. Phasellus nec eros mauris, et scelerisque orci.</p>
    <p>Donec malesuada orci vitae nulla accumsan porta a id massa. Quisque accumsan iaculis magna sit amet fringilla. Maecenas consequat, magna eget tincidunt semper, odio nibh rutrum mi, id feugiat ante nisi eu risus. Vestibulum nunc orci, rhoncus a placerat in, ultricies in mi. Cras mattis varius eros, vel fringilla nisi suscipit eget. Quisque scelerisque sagittis nulla at porttitor.</p>
    <p>Sed id augue vitae urna euismod commodo aliquet a quam. Pellentesque arcu velit, cursus et malesuada ut, consequat et diam. Nullam erat sem, rhoncus id ullamcorper vitae, rhoncus et arcu. In ultricies ultricies nulla, ut rutrum nisi iaculis at. Donec eu magna a metus ornare faucibus. Fusce aliquet faucibus ultricies. Morbi semper, est id tincidunt gravida, sem arcu adipiscing lacus, ac bibendum nulla leo eu purus. Quisque nec diam sed risus consectetur a ccumsan quis quis nibh. Vestibulum id purus lorem.</p>
  </div>
  <div class="signoff">Sincerely,</div>
  <div class="signature" role="img" aria-label="Handwritten signature of Ned Farrow"></div>
  <svg class="wave bottom-wave" viewBox="0 0 372 92" preserveAspectRatio="none" aria-hidden="true">
    <path d="M0 14 C120 -4 240 24 372 4 V92 H0 Z" fill="var(--sky)"/>
    <path d="M0 22 C120 4 240 32 372 12 V92 H0 Z" fill="var(--paper)" opacity=".35"/>
  </svg>
  <div class="legal">ABN 38 602 917 255<br>Beatrix Lund atf The BJL Legal Trust t/as Harbour Gate Legal &amp; Conveyancing</div>
  <div class="foot">
    <div>Address: Wexley House, Wexley Street, Albany<br>Postal Address: PO Box 8147, Albany WA 6332</div>
    <div>Email: info@harbourgatelegal.com.au<br>Website: www.harbourgatelegal.com.au</div>
  </div>
</section>

<!-- With compliments slip -->
<section class="piece comp-slip" aria-label="With compliments slip">
  <svg class="wave" viewBox="0 0 392 168" preserveAspectRatio="none" aria-hidden="true">
    <path d="M0 52 C110 60 160 10 250 8 C320 6 360 20 392 0 V168 H0 Z" fill="var(--sky)"/>
  </svg>
  <div class="brand-name"><span class="dot"></span><span>Harbour Gate<br>Legal &amp; Conveyancing</span></div>
  <div class="headline">WITH COMPLIMENTS</div>
  <div class="legal">ABN 38 602 917 255<br>Beatrix Lund atf The BJL Legal Trust t/as Harbour Gate Legal &amp; Conveyancing</div>
  <div class="contacts">
    <div><b>Email:</b> info@harbourgatelegal.com.au<br><b>Website:</b> www.harbourgatelegal.com.au</div>
    <div><b>Telephone:</b> 0491 670 382<br><b>Facsimile:</b> 08 9722 5913</div>
    <div><b>Address:</b> Wexley House, Wexley Street, Albany<br><b>Postal Address:</b> PO Box 8147, Albany WA 6332</div>
  </div>
</section>

<!-- Flyer -->
<section class="piece flyer" aria-label="Services flyer">
  <div class="photo" role="img" aria-label="Photo of a person walking along a timber jetty over blue ocean water"></div>
  <svg class="wave cap" viewBox="0 0 400 86" preserveAspectRatio="none" aria-hidden="true">
    <path d="M0 0 H170 C150 30 140 60 120 86 H0 Z" fill="var(--paper)"/>
  </svg>
  <div class="brand-name"><span class="dot"></span><span>Harbour Gate<br>Legal &amp; Conveyancing</span></div>
  <ul class="services">
    <li>Wills &amp; Estate Planning</li>
    <li>Probate &amp; Letters of Administration</li>
    <li>Property Law &amp; Conveyancing</li>
    <li>General Commercial Law</li>
    <li>Business Law</li>
  </ul>
  <div class="tel">Telephone: 0491 670 382</div>
  <div class="links"><span>info@harbourgatelegal.com.au</span><span>www.harbourgatelegal.com.au</span></div>
</section>

</body>
</html>
```